Wordpress Design Project

We are a local restaurant who needs a quality online identity base. We operate in a 1930's Villa, and our target market is the below mid - upper. Our main sale is the evening dinner meal, while we also sell home-made goods, including preserves, and handmade chocolates.
The final Wordpress coded design will:
Be a base for information including Contact details, and a Map of it's location. It will also include photographs of some of the dishes to give an idea to potential customers as to the style and target market.
The site will have 4 main pages
-Main
-About
-Menu
-Contact
Ideas for elements we would like to have included in the design are
Cardboard tags with the links to the other pages, which give a home-made feel
Character wood, with deep grain to emphasis our homely feel
An 'aged' map of the location. Possibly on a large cardboard tag.
Link to our Facebook page
Link to our Plate Finder review page http://www.platefinder.co.nz/restaurant.php?rest=3927
Notes:
The final Wordpress site should communicate a homely inviting image, with deep character, while still looking elegant and slightly simplistic. We would like fine fonts, with nice spacing, especially on the cardboard tags.
I have attached a mockup of our very loose vision for the site to give you an idea of the line we would like to go down. This is just for initial ideas, and we are happy for radically different designs, or just neat variations on the base design
Professional, edited photos of the food available will be uploaded alongside this project
Villa Serena does not have an official Logo for use on the website, so a simple header that ties in with the page will be fine. This may be replaced eventually with a new logo
Address and Hosting is already setup with the address being www.villaserenakitchen.co.nz with a placeholder site online.
We look forward to all designs, and welcome any questions. This should be an nice job for someone with an eye for detail.

```html
<!DOCTYPE html>
<html lang="en">
<head>
<meta charset="utf-8">
<title>Villa Serena – The Restaurant</title>
<link href="https://fonts.googleapis.com/css2?family=Arimo:wght@400;700&family=Questrial&family=Noto+Serif:ital@1&display=swap" rel="stylesheet">
<style>
:root{
  --page-black:#050505;
  --panel-black:#141414;
  --panel-edge:#2a2a2a;
  --accent-red:#c8101a;
  --deep-red:#8e0a10;
  --nav-grey:#555;
  --bar-grey:#5a5a5a;
  --body-grey:#8d8d8d;
  --light-grey:#c9c9c9;
  --heading-white:#e4e4e4;
  --wood-dark:#3a1f10;
  --wood-mid:#6b3b1f;
  --wood-light:#a8703f;
  --tag-paper:rgba(235,235,235,.86);
  --tag-ink:#111;
}
*{box-sizing:border-box;margin:0;padding:0}
html,body{width:1200px;height:1019px;overflow:hidden;background:var(--page-black)}
body{font-family:"Arimo",Arial,sans-serif;position:relative}
.canvas{position:relative;width:1200px;height:1019px;overflow:hidden;background:var(--page-black)}
.side-scene{position:absolute;top:0;width:200px;height:560px}
.side-scene.left{left:0;background:radial-gradient(ellipse at 60% 30%,#6a5433 0%,#3a2d1c 40%,#120d08 75%,var(--page-black) 100%)}
.side-scene.right{right:0;background:radial-gradient(ellipse at 40% 35%,#7a6446 0%,#45362a 40%,#150f0a 75%,var(--page-black) 100%)}
.column{position:absolute;left:200px;top:0;width:800px;height:1019px;background:linear-gradient(#1a1a1a,#0d0d0d)}
.header{position:absolute;left:0;top:0;width:800px;height:328px;background:repeating-linear-gradient(90deg,#f4f4f4 0 14px,#ececec 14px 28px)}
.brand{position:absolute;left:62px;top:30px;display:flex;align-items:center;gap:10px;font-family:"Questrial",sans-serif;font-size:30px;color:var(--accent-red)}
.brand-dot{width:14px;height:14px;border-radius:50%;background:var(--accent-red)}
.nav{position:absolute;left:518px;top:24px;width:266px;height:28px;border-bottom:4px solid var(--bar-grey);display:flex;justify-content:space-between}
.nav a{font-family:"Noto Serif",serif;font-style:italic;font-size:13px;color:var(--nav-grey);text-decoration:none;padding:0 4px}
.nav a.current{color:var(--accent-red);border-bottom:4px solid var(--accent-red);margin-bottom:-4px;padding:0 2px}
.hero{position:absolute;left:16px;top:78px;width:768px;height:212px;border:3px solid #bbb;border-radius:8px;background:linear-gradient(90deg,#d8c4a8 0%,#8a5a2e 20%,#3f5a22 30%,#efe6dc 48%,#b7a3c6 60%,#6e4c2e 75%,#c19a6a 90%,#e8d4b2 100%)}
.intro-panel{position:absolute;left:16px;top:307px;width:768px;height:242px;background:var(--panel-black);border:1px solid var(--panel-edge);border-radius:6px}
.section-title{position:absolute;font-family:"Questrial",sans-serif;font-weight:400;font-size:16px;color:var(--heading-white);white-space:nowrap}
.section-title em{font-style:normal;color:var(--accent-red)}
.body-copy{position:absolute;font-size:9px;text-align:justify}
.welcome-copy{left:16px;top:40px;width:264px;line-height:17.5px;color:var(--light-grey)}
.welcome-copy p+p{margin-top:3px}
.chain{position:absolute;left:290px;top:-18px}
.menu-board{position:absolute;left:297px;top:56px;width:239px;height:194px;border-radius:5px;background:repeating-linear-gradient(88deg,var(--wood-light) 0 5px,#9a6233 5px 9px,#b57c48 9px 14px);box-shadow:0 2px 6px rgba(0,0,0,.6)}
.menu-board h3{position:absolute;left:0;top:7px;width:100%;text-align:center;font-family:"Questrial",sans-serif;font-weight:400;font-size:15px;color:#fff}
.dish-photo{position:absolute;border:3px solid #fff;border-radius:8px}
.menu-board .dish-photo{left:18px;top:42px;width:98px;height:122px;border-color:#3a2412;background:radial-gradient(circle at 50% 65%,#6a4a2a 0%,#e9e2d6 45%,#4a3420 100%)}
.menu-copy{left:127px;top:44px;width:101px;color:#fff;line-height:13px}
.menu-copy p+p{margin-top:5px}
.detail-btn{position:absolute;left:169px;top:164px;width:55px;height:19px;background:linear-gradient(#b01018,var(--deep-red));color:#fff;font-size:11px;text-align:center;line-height:19px;border-radius:2px}
.arrow{position:absolute;left:650px}
.category-name{position:absolute;left:571px;top:66px;font-family:"Questrial",sans-serif;font-size:16px;color:#cfcfcf}
.intro-panel .category-photo{left:557px;top:93px;width:95px;height:100px;background:radial-gradient(circle at 50% 55%,#8a3a1c 0%,#e8ddd0 45%,#2b1c12 100%)}
.category-copy{left:667px;top:91px;width:79px;color:#a8a8a8;line-height:13px}
.category-copy .more{margin-top:8px;letter-spacing:1px;text-align:left}
.bar-photo{position:absolute;left:32px;top:586px;width:327px;height:183px;border-radius:6px;background:linear-gradient(100deg,#2a1608 0%,#a46a26 25%,#5a1a12 45%,#d19a48 65%,#3a2410 85%,#c78a3a 100%);box-shadow:0 0 0 2px #d87a1a}
.bar-copy{left:376px;top:584px;width:394px;line-height:17.5px;color:var(--body-grey)}
.bar-copy p+p{margin-top:5px}
.hours-band{position:absolute;left:0;top:787px;width:800px;height:232px;background:repeating-linear-gradient(90deg,var(--wood-mid) 0 3px,#5a2f18 3px 7px,#74411f 7px 11px,var(--wood-dark) 11px 13px)}
.hours-band::after{content:"";position:absolute;inset:0;background:linear-gradient(rgba(0,0,0,.15),rgba(0,0,0,.35) 60%,rgba(0,0,0,.85))}
.hours-tag{position:absolute;top:29px;width:164px;height:90px;background:var(--tag-paper);z-index:1;text-align:center;color:var(--tag-ink)}
.hours-tag::before{content:"";position:absolute;left:73px;top:-14px;width:18px;height:20px;background:rgba(230,230,230,.55)}
.hours-tag h4{font-weight:400;font-size:14.5px;margin-top:12px}
.hours-tag dl{font-size:9.5px;line-height:16px;margin-top:4px;display:grid;grid-template-columns:auto auto;justify-content:center;column-gap:6px}
.hours-tag dt{text-align:right}
.hours-tag dd{text-align:left;color:var(--tag-ink)}
.footer{position:absolute;left:16px;top:932px;width:771px;display:flex;justify-content:space-between;font-size:10px;color:#9a9a9a;z-index:1}
.footer nav span{margin:0 10px}
</style>
</head>
<body>
<div class="canvas">
  <div class="side-scene left" role="img" aria-label="Warm restaurant table scene with menus and pepper mills"></div>
  <div class="side-scene right" role="img" aria-label="Shelf of home-made preserves and chocolate jars"></div>

  <main class="column">
    <header class="header">
      <div class="brand"><span class="brand-dot"></span>Villa Serena</div>
      <nav class="nav">
        <a class="current" href="#">Home</a><a href="#">About Us</a><a href="#">Menu</a><a href="#">Contact</a>
      </nav>
      <div class="hero" role="img" aria-label="Plated dinner dish beside flowers and a wooden wine crate"></div>
    </header>

    <section class="intro-panel">
      <h2 class="section-title" style="left:16px;top:14px">Welcome to <em>Villa Serena</em></h2>
      <div class="body-copy welcome-copy">
        <p>Lorem ipsum dolor sit amet, consectetur adipiscing elit. Nullam ultricies commodo semper. In volutpat, risus a pretium fringilla, mauris elit tempus eros, non porta lorem ipsum non tortor. Sed dapibus adipiscing massa, ac dictum nunc tempus sed. Nulla facilisi. Fusce blandit sapien non risus blandit laoreet varius nec nisi. Vestibulum ante ipsum primis in faucibus orci luctus et ultrices posuere cubilia Curae; Maecenas laoreet lorem vel ipsum malesuada vel iaculis ante iaculis. Morbi vitae nisi quis dui gravida faucibus.</p>
        <p>Nulla facilisi. Fusce blandit sapien non risus blandit laoreet</p>
      </div>

      <svg class="chain" width="260" height="90" viewBox="0 0 260 90" aria-hidden="true">
        <polyline points="33,88 130,10 227,88" fill="none" stroke="#6d6d6d" stroke-width="4" stroke-dasharray="6 3"/>
        <circle cx="130" cy="10" r="4" fill="#888"/>
        <circle cx="33" cy="88" r="3" fill="#222"/><circle cx="227" cy="88" r="3" fill="#222"/>
      </svg>
      <div class="menu-board">
        <h3>New in menu</h3>
        <div class="dish-photo" role="img" aria-label="New dinner dish with a glass of red wine"></div>
        <div class="body-copy menu-copy">
          <p>Lorem ipsum dolor sit amet, consectetur adipi&shy;scing elit. Nullam ultri&shy;cies commodo semper.</p>
          <p>Lorem ipsum dolor sit amet, consectetur adipi&shy;scing elit. Nullam ultri&shy;cies commodo semper.</p>
        </div>
        <a class="detail-btn">Detail</a>
      </div>

      <h2 class="section-title" style="left:549px;top:14px"><em>C</em>ategory</h2>
      <svg class="arrow" style="top:45px" width="28" height="10" viewBox="0 0 28 10" aria-hidden="true"><polygon points="0,9 14,1 28,9" fill="#777"/></svg>
      <div class="category-name">Chocolates</div>
      <div class="dish-photo category-photo" role="img" aria-label="Chocolate dessert with cream"></div>
      <div class="body-copy category-copy">
        <p>Lorem ipsum dolor sit amet, consect&shy;etur adipiscing elit. Nullam ultricies commodo semper.</p>
        <p class="more">Loremipadcing Lorem...</p>
      </div>
      <svg class="arrow" style="top:213px" width="28" height="10" viewBox="0 0 28 10" aria-hidden="true"><polygon points="0,1 14,9 28,1" fill="#777"/></svg>
    </section>

    <h2 class="section-title" style="left:31px;top:561px">Bar <em>and</em> Cafe</h2>
    <div class="bar-photo" role="img" aria-label="Candlelit bar table with wine glasses and pepper mills"></div>
    <div class="body-copy bar-copy">
      <p>Lorem ipsum dolor sit amet, consectetur adipiscing elit. Aenean varius tempus arcu eu condi&shy;mentum. Class aptent taciti sociosqu ad litora torquent per conubia nostra, per inceptos hime&shy;naeos. Proin facilisis dignissim eros, vel mattis mi lacinia ut. Fusce vitae mauris ac enim ves&shy;tibulum scelerisque. Duis convallis adipiscing posuere. Praesent id felis quis arcu auctor sagit&shy;tis. Integer lacinia enim tortor. Maecenas eu libero mattis nunc suscipit iaculis.</p>
      <p>Lorem ipsum dolor sit amet, consectetur adipiscing elit. Aenean varius tempus arcu eu condi&shy;mentum. Class aptent taciti sociosqu ad litora torquent per conubia nostra, per inceptos hime&shy;naeos. Proin facilisis dignissim eros, vel mattis mi lacinia ut. Fusce vitae mauris ac enim ves&shy;tibulum scelerisque. Duis convallis adipiscing posuere. Praesent id felis quis arcu auctor sagit&shy;tis. Integer lacinia enim tortor. Maecenas eu libero mattis nunc suscipit iaculis.</p>
    </div>

    <section class="hours-band">
      <div class="hours-tag" style="left:77px">
        <h4>Bar and Cafe</h4>
        <dl><dt>Monday - Saturday</dt><dd>10 a.m - 10 p.m</dd><dt>Sunday</dt><dd>10 a.m - 12 p.m</dd></dl>
      </div>
      <div class="hours-tag" style="left:322px">
        <h4>Lunch</h4>
        <dl><dt>Monday - Friday</dt><dd>11 a.m - 1 a.m</dd><dt>Saturday - Sunday</dt><dd>11 a.m - 3 p.m</dd></dl>
      </div>
      <div class="hours-tag" style="left:565px">
        <h4>Dinner</h4>
        <dl><dt>Monday - Friday</dt><dd>6 a.m - 10 p.m</dd><dt>Saturday - Sunday</dt><dd>6 a.m - 12 p.m</dd></dl>
      </div>
    </section>

    <footer class="footer">
      <span>All Rights Reserved@Villa Serena</span>
      <nav>Home<span>|</span>About<span>|</span>Contact<span>|</span>Terms</nav>
    </footer>
  </main>
</div>
</body>
</html>
```